New Business Card Design Project LORVANTI-Italy

we are LORVANTI-Italy
our company in the market for 3 years we are luxury cosmetic company and its about time for a facelift :)
i will like to have elegant luxurious and unique business card
that will give the person that get it a unique, luxurious and elegant impression
I'm VERY OPEN FOR NEW IDEAS , even duo i add a few files of things that i see on line and i like them

i add my logo as well
my website is LORVANTI.COM
(if you would like to see the main style that we have)

Target Market(s)

adult that have money :)

Industry/Entity Type

Business

Contact Information for Business Card

Name - Dario Lorvanti
Position - CEO and CO Founder
address - 4817 E Halvern
telephone - 555-384-1926
email - dario@lorvanti.com
fax - 555-384-1926
website - LORVANTI.COM

Colors
000000
959595
fbee3e
ffffff

Requirements
Must have
• big logo in GOLD color
• elegant look
• impressive
Nice to have
• not must but maybe classy pattern background
• not must but maybe emblem
• maybe clear plastic business card
Should not have
• colors
• images

```html
<!DOCTYPE html>
<html lang="en">
<head>
<meta charset="utf-8">
<title>LORVANTI Italy – Business Card</title>
<link href="https://fonts.googleapis.com/css2?family=Cinzel:wght@500&family=Open+Sans:wght@400;600&display=swap" rel="stylesheet">
<style>
  :root {
    --stage: #2b2927;
    --card-dark: #0c0c0c;
    --card-mid: #1a1a1a;
    --tab: #2c2c2c;
    --tab-shade: #1f1f1f;
    --gold: #e3b52d;
    --gold-light: #fbe16a;
    --ink: #0b0b0b;
    --pattern: #262626;
  }
  * { margin: 0; padding: 0; box-sizing: border-box; }
  html, body {
    width: 1200px; height: 1200px; overflow: hidden;
    background: var(--stage);
  }
  .card {
    position: absolute; left: 80px; top: 300px;
    width: 1040px; height: 600px;
    border-radius: 24px;
    background: linear-gradient(135deg, var(--card-mid) 0%, var(--card-dark) 55%, var(--card-mid) 100%);
    overflow: hidden;
    box-shadow: 0 30px 60px rgba(0,0,0,.55);
  }
  .card__pattern {
    position: absolute; left: 20px; top: 60px;
    width: 380px; height: 620px;
    border-radius: 50% 50% 0 0 / 40% 40% 0 0;
    background: radial-gradient(ellipse at 60% 40%, var(--pattern) 0%, rgba(38,38,38,.35) 55%, transparent 75%);
    opacity: .8;
  }
  .brand {
    position: absolute; left: 40px; top: 70px;
    width: 500px;
    display: flex; flex-direction: column; align-items: center;
  }
  .brand__mark {
    width: 160px; height: 160px; border-radius: 50%;
    border: 8px solid var(--gold);
  }
  .brand__name, .brand__origin {
    font-family: "Cinzel", "Times New Roman", serif;
    font-weight: 500; color: var(--gold);
  }
  .brand__name {
    margin-top: 36px; font-size: 84px; line-height: 1; letter-spacing: 1px;
  }
  .brand__rule {
    width: 380px; height: 4px; margin-top: 16px;
    background: var(--gold);
  }
  .brand__origin {
    margin-top: 16px; font-size: 40px; letter-spacing: 3px;
  }
  .contacts {
    position: absolute; left: 580px; top: 70px;
    list-style: none;
  }
  .contact {
    display: flex; align-items: center;
    height: 48px; margin-bottom: 34px;
  }
  .contact__tab {
    width: 54px; height: 48px;
    background: linear-gradient(180deg, var(--tab) 0%, var(--tab-shade) 100%);
  }
  .contact__icon {
    width: 48px; height: 48px;
    background: linear-gradient(135deg, var(--gold-light), var(--gold));
    display: flex; align-items: center; justify-content: center;
  }
  .contact__icon svg { width: 30px; height: 30px; fill: var(--ink); }
  .contact__text {
    margin-left: 22px;
    font-family: "Open Sans", Arial, sans-serif;
    font-size: 25px; color: var(--gold); line-height: 1.15;
  }
  .contact__text strong { display: block; font-weight: 600; font-size: 30px; }
  .contact__text small { display: block; font-size: 21px; }
</style>
</head>
<body>
  <article class="card">
    <div class="card__pattern" role="img" aria-label="Faint ornamental lace pattern in dark grey behind the brand block"></div>

    <div class="brand">
      <div class="brand__mark"></div>
      <div class="brand__name">LORVANTI</div>
      <div class="brand__rule"></div>
      <div class="brand__origin">ITALY</div>
    </div>

    <ul class="contacts">
      <li class="contact">
        <span class="contact__tab"></span>
        <span class="contact__icon"><svg viewBox="0 0 24 24"><circle cx="12" cy="7" r="4.5"/><path d="M3 22c0-5 4-8 9-8s9 3 9 8z"/></svg></span>
        <span class="contact__text"><strong>Dario Lorvanti</strong><small>CEO and CO Founder</small></span>
      </li>
      <li class="contact">
        <span class="contact__tab"></span>
        <span class="contact__icon"><svg viewBox="0 0 24 24"><path d="M12 2a7 7 0 0 0-7 7c0 5 7 13 7 13s7-8 7-13a7 7 0 0 0-7-7zm0 10a3 3 0 1 1 0-6 3 3 0 0 1 0 6z"/></svg></span>
        <span class="contact__text">4817 E Halvern</span>
      </li>
      <li class="contact">
        <span class="contact__tab"></span>
        <span class="contact__icon"><svg viewBox="0 0 24 24"><path d="M6.6 10.8a15 15 0 0 0 6.6 6.6l2.2-2.2a1 1 0 0 1 1-.25 11.4 11.4 0 0 0 3.6.57 1 1 0 0 1 1 1V20a1 1 0 0 1-1 1A17 17 0 0 1 3 4a1 1 0 0 1 1-1h3.5a1 1 0 0 1 1 1c0 1.25.2 2.45.57 3.57a1 1 0 0 1-.25 1z"/></svg></span>
        <span class="contact__text">555-384-1926</span>
      </li>
      <li class="contact">
        <span class="contact__tab"></span>
        <span class="contact__icon"><svg viewBox="0 0 24 24"><path d="M2 5h20v14H2zm2 2v.5l8 5 8-5V7l-8 5z"/></svg></span>
        <span class="contact__text">dario@lorvanti.com</span>
      </li>
      <li class="contact">
        <span class="contact__tab"></span>
        <span class="contact__icon"><svg viewBox="0 0 24 24"><path d="M7 2h9l3 3v5H7zM4 10h16a2 2 0 0 1 2 2v8a2 2 0 0 1-2 2H4a2 2 0 0 1-2-2v-8a2 2 0 0 1 2-2zm3 4v2h10v-2z"/></svg></span>
        <span class="contact__text">555-384-1926</span>
      </li>
      <li class="contact">
        <span class="contact__tab"></span>
        <span class="contact__icon"><svg viewBox="0 0 24 24"><path d="M12 2a10 10 0 1 0 0 20 10 10 0 0 0 0-20zm6.9 9h-3a15 15 0 0 0-1.3-6 8 8 0 0 1 4.3 6zM12 4c1 1.3 1.8 3.8 1.9 7h-3.8C10.2 7.8 11 5.3 12 4zM9.4 5a15 15 0 0 0-1.3 6h-3a8 8 0 0 1 4.3-6zM5.1 13h3a15 15 0 0 0 1.3 6 8 8 0 0 1-4.3-6zM12 20c-1-1.3-1.8-3.8-1.9-7h3.8c-.1 3.2-.9 5.7-1.9 7zm2.6-1a15 15 0 0 0 1.3-6h3a8 8 0 0 1-4.3 6z"/></svg></span>
        <span class="contact__text">LORVANTI.COM</span>
      </li>
    </ul>
  </article>
</body>
</html>
```